Business Cards for IT Consulting Company (Managed Service Provider)

I am looking to have some business cards printed and would like some designs. We are an IT Consulting company based in Vancouver BC. I would like a nice clean and modern look to the cards. I have uploaded all the versions of my logo so parts can be used as needed. Here is a snippit from our website homepage:

Quillbrook Networks Ltd. is an IT Solutions Partner located in Vancouver BC, Canada. We offer IT solutions and support to customers in the greater Vancouver Area. With expertise in Microsoft platforms, as well as Linux and Mac OSX and over 12 years experience in the IT industry, Quillbrook Networks is dedicated to offering our clients top quality service and products. We take pride in the solutions we offer our customers. The greatest compliment a client can give us is to recommend our services.

Quillbrook Networks Ltd. offers a wide range of IT services from onsite service to remote support and managed service solutions. This allows clients to choose the support path that best suits their company’s needs. Supporting many different sized companies from small to enterprise level over the past 12 years Quillbrook Networks has the experience and expertise needed to ensure things run smoothly. Allowing our clients to focus on doing business.

Revolutionizing the way IT services are delivered.

Quillbrook Networks is dedicated to providing our clients with IT solutions that work and grow with them for years to come. This philosophy helps save money in the long run instead of replacing equipment constantly. Far too often IT solutions are not well thought out and while possibly solving the problem at hand, require replacement due to growth or quality within a very short time frame. Quillbrook Networks takes pride in providing solutions that will last and be able to accommodate growth without the need for replacement.

Industry/Entity Type

Information Technology

Contact Information for Business Card

Quillbrook Networks Ltd.
(Employee Name)
Eml: (Employees Email Address)
Web: quillbrook.me
Ph: 604-555-0148

Font styles to use
Serif
Sans Serif

Requirements
Must have
• The Company logo and company colors.
Nice to have
• - Our tag line: "Revolutionizing IT Services" or "Revolutionizing the way IT services are delivered."
• - Also I really like the idea of nature and technology together blending which is sort of where my logo came from so integrating that somehow onto the business cards would be great.

```html
<!DOCTYPE html>
<html lang="en">
<head>
<meta charset="utf-8">
<title>Quillbrook Networks Ltd. — Business Cards</title>
<link href="https://fonts.googleapis.com/css2?family=Montserrat:wght@400;500;600;700&family=Roboto:ital,wght@0,400;1,400&display=swap" rel="stylesheet">
<style>
  :root {
    --backdrop: #a8a6a7;
    --card-dark: #1f1f20;
    --card-light: #efefef;
    --brand-blue: #1f8fd4;
    --brand-grey: #59585a;
    --text-dark: #333335;
    --text-muted: #555557;
    --white: #ffffff;
    --divider: #dcdcdc;
  }
  * { box-sizing: border-box; margin: 0; padding: 0; }
  html, body { width: 1200px; height: 1200px; overflow: hidden; }
  body {
    background: var(--backdrop);
    position: relative;
    font-family: "Montserrat", sans-serif;
  }

  .card { position: absolute; overflow: hidden; }

  /* Front */
  .card-front {
    left: 238px; top: 117px; width: 714px; height: 420px;
    background: var(--card-dark);
  }
  .front-brand {
    position: absolute; left: 0; right: 0; top: 170px;
    display: flex; align-items: center; justify-content: center; gap: 22px;
  }
  .brand-square {
    width: 46px; height: 46px;
    border: 4px solid var(--brand-blue);
  }
  .brand-name {
    font-family: "Montserrat", sans-serif;
    font-weight: 600;
    font-size: 40px;
    color: var(--brand-blue);
    letter-spacing: 0.5px;
  }
  .front-tagline {
    position: absolute; left: 0; right: 0; top: 377px;
    display: flex; align-items: center; justify-content: center; gap: 18px;
  }
  .tagline-rule { width: 108px; height: 3px; background: var(--brand-blue); }
  .tagline-text {
    font-family: "Montserrat", sans-serif;
    font-weight: 500; font-size: 18px; color: var(--white);
    letter-spacing: 0.2px;
  }

  /* Back */
  .card-back {
    left: 230px; top: 644px; width: 713px; height: 417px;
    background: var(--card-light);
  }
  .back-mark {
    position: absolute; left: 60px; top: 110px; width: 215px;
    display: flex; flex-direction: column; align-items: center; gap: 18px;
  }
  .mark-circle {
    width: 120px; height: 120px; border-radius: 50%;
    border: 5px solid var(--brand-blue);
  }
  .mark-name {
    font-family: "Montserrat", sans-serif;
    font-weight: 600; font-size: 17px; color: var(--brand-blue);
    text-align: center; line-height: 1.3;
  }
  .back-divider {
    position: absolute; left: 331px; top: 80px; width: 1px; height: 248px;
    background: var(--divider);
  }
  .contact-block { position: absolute; left: 390px; top: 122px; }
  .person-name {
    font-family: "Montserrat", sans-serif;
    font-weight: 700; font-size: 26px; color: var(--brand-blue);
  }
  .person-title {
    font-family: "Roboto", sans-serif;
    font-style: italic; font-size: 16px; color: var(--text-muted);
    margin-top: 6px;
  }
  .contact-list { list-style: none; margin-top: 24px; }
  .contact-item {
    display: flex; align-items: center; gap: 17px;
    font-family: "Roboto", sans-serif; font-size: 18px; color: var(--text-dark);
    height: 27px;
  }
  .contact-icon { width: 18px; height: 18px; flex: none; }
  .back-band-grey {
    position: absolute; left: 0; bottom: 0; width: 340px; height: 26px;
    background: var(--brand-grey);
  }
  .back-band-blue {
    position: absolute; left: 315px; bottom: 0; width: 398px; height: 53px;
    background: var(--brand-blue);
    clip-path: polygon(28px 0, 100% 0, 100% 100%, 0 100%);
    display: flex; align-items: center; padding-left: 75px;
  }
  .band-tagline {
    font-family: "Montserrat", sans-serif;
    font-weight: 500; font-size: 19px; color: var(--white);
  }
</style>
</head>
<body>

<section class="card card-front" aria-label="Business card front">
  <div class="front-brand">
    <span class="brand-square"></span>
    <span class="brand-name">Quillbrook Networks Ltd.</span>
  </div>
  <div class="front-tagline">
    <span class="tagline-rule"></span>
    <span class="tagline-text">Revolutionizing IT Services</span>
    <span class="tagline-rule"></span>
  </div>
</section>

<section class="card card-back" aria-label="Business card back">
  <div class="back-mark">
    <span class="mark-circle"></span>
    <span class="mark-name">Quillbrook Networks Ltd.</span>
  </div>
  <div class="back-divider"></div>

  <div class="contact-block">
    <h1 class="person-name">Martin Hale</h1>
    <p class="person-title">Managing Director</p>
    <ul class="contact-list">
      <li class="contact-item">
        <svg class="contact-icon" viewBox="0 0 20 20" aria-hidden="true">
          <path d="M2 7c0-3 4-4 8-4s8 1 8 4v1.5h-4V7c-1-.6-7-.6-8 0v1.5H2z" fill="var(--brand-blue)"/>
          <path d="M5 9h10l2 8H3z" fill="var(--brand-blue)"/>
          <circle cx="10" cy="13" r="2" fill="var(--card-light)"/>
        </svg>
        <span>604-555-0148</span>
      </li>
      <li class="contact-item">
        <svg class="contact-icon" viewBox="0 0 20 20" aria-hidden="true" fill="none" stroke="var(--brand-blue)" stroke-width="1.6">
          <circle cx="10" cy="10" r="7.5"/>
          <ellipse cx="10" cy="10" rx="3.2" ry="7.5"/>
          <path d="M2.5 10h15M4 6h12M4 14h12"/>
        </svg>
        <span>www.quillbrook.me</span>
      </li>
      <li class="contact-item">
        <svg class="contact-icon" viewBox="0 0 20 20" aria-hidden="true">
          <rect x="1.5" y="4" width="17" height="12" fill="var(--brand-blue)"/>
          <path d="M2 4.5l8 6 8-6" fill="none" stroke="var(--card-light)" stroke-width="1.4"/>
        </svg>
        <span>support@quillbrook.me</span>
      </li>
    </ul>
  </div>

  <div class="back-band-grey"></div>
  <div class="back-band-blue"><span class="band-tagline">Revolutionizing IT Services</span></div>
</section>

</body>
</html>
```